Online Shop Maren

We need a web design for an online shop, called "Lirvo Dune Jewels". The shop should have an extraordinary, elegant look, as shown in the Quellwick Advertising Picture in our Briefing.pdf (attached). Please have a look at our Briefing regarding website colours, background ideas, and elements to be included. The online shop is about professional jewellery design pieces, where each piece is handmade of high quality materials, also unique pieces and unique editions possible. It should attract extraordinary people and visualize that its a very individual and unique design jewellery. You can get an idea of whom it should attract by reading our target group. Colours to be used are jewellery-Velvet red, Black / anthracite, exclusive colours, silverish-white, bronze-brown and golden.

Please play around when designing with the image pictures we attach, preferably more vertical pictures, no panoramic pictures like in Brovenka Shop. Also include the BLACK logo of lirvo dune. We include the SITEMAP in the briefing and also another folder with product pictures you can use for the draft.

Regarding Functions, the store will have the SAME (technical) functions as this page:http://www.brovenka-shop.eu/ - using the "most famous" products/categories for the starting page, going into individual product pages by clicking these images and then leading to a detailed page for one product only.

Target Market(s)

Jewellery-lovers, who appreciate extraordinary things, creative economy/fashion-industries, stylists, Style consultants, outfitter, theatres, operas, production sites, Cocktail-, Dinner and Bridefashion, exclusive traditional costume stores, dancesports and tango argento dancers

Industry/Entity Type

Shop

Requirements
Must have
• Must include:
• Colours as per briefing
• Background ideas/images as per briefing/pictures sent
• Sitemap as per briefing
• Social buttons
• Logo
• Design for 3 pages: Starting page showing big images, attractive design and the 4 popular categories
• Subpage with different products of one category (i.e. bracelets)
• Detail page with one individual product only
Should not have
• no fresh, playful colours like yellow, orange, green, blue
• no cheap design, no panorama pictures

```html
<!DOCTYPE html>
<html lang="de">
<head>
<meta charset="utf-8">
<title>Lirvo Dune Jewels</title>
<link rel="stylesheet" href="https://fonts.googleapis.com/css2?family=Cinzel:wght@400;700&family=Dosis:wght@400;500&family=Open+Sans:wght@400;600&display=swap">
<style>
:root{
  --bg:#1b1b1b;
  --wood-top:#2c2824;
  --wood-mid:#221f1c;
  --panel:#161616;
  --panel-head:#202020;
  --line:#3a3a3a;
  --text:#d8d8d8;
  --muted:#9a9a9a;
  --white:#f2f2f2;
  --gold:#d9a93a;
  --gold-light:#f3ce6a;
  --gold-dark:#c48f24;
  --nav-text:#3b2a10;
}
*{margin:0;padding:0;box-sizing:border-box}
html,body{width:947px;height:1200px;overflow:hidden;background:var(--bg)}
body{position:relative;font-family:"Open Sans",sans-serif;color:var(--text)}
.abs{position:absolute}
.header-bg{left:0;top:0;width:947px;height:360px;
  background:repeating-linear-gradient(90deg,rgba(255,255,255,.025) 0 2px,transparent 2px 38px),
  linear-gradient(180deg,var(--wood-top) 0%,var(--wood-mid) 70%,var(--bg) 100%)}
.logo{left:0;width:947px;top:24px;text-align:center;font-family:"Open Sans",sans-serif;font-weight:400;color:var(--white)}
.logo .name{font-size:37px;line-height:46px;letter-spacing:.5px}
.logo .sub{font-size:20px;line-height:26px;margin-top:2px}
.social{left:85px;top:79px;display:flex;gap:3px}
.social span{width:23px;height:23px;border-radius:50%;background:var(--white);display:block}
.cart{left:770px;top:30px;width:89px;height:32px;border:1px solid #555;border-radius:16px;background:#1c1c1c;
  color:var(--white);font-size:12px;display:flex;align-items:center;justify-content:center;gap:4px}
.search{left:673px;top:78px;width:192px;height:26px;border:1px solid #555;background:#1d1d1d;
  font-size:10px;font-style:italic;color:#bbb;padding-left:9px;line-height:24px}
.search svg{position:absolute;right:7px;top:5px}
.nav{left:80px;top:118px;width:786px;height:37px;
  background:linear-gradient(180deg,var(--gold-light) 0%,var(--gold) 60%,var(--gold-dark) 100%);
  display:flex;justify-content:center;align-items:center;gap:14px;
  font-family:"Cinzel",serif;font-size:14.5px;color:var(--nav-text);letter-spacing:.6px}
.nav .sep{font-size:10px}
.hero{left:80px;top:156px;width:786px;height:218px;
  background:linear-gradient(100deg,#8e8c8f 0%,#5b4a58 25%,#c79a86 45%,#e2b8a2 65%,#d9d2cc 85%,#a8a29c 100%);
  border-right:3px solid #111}
.hero-title{left:80px;top:220px;width:786px;text-align:center;font-family:"Cinzel",serif;color:#fff3d8;
  font-size:34px;line-height:42px;text-shadow:0 1px 3px rgba(0,0,0,.4)}
.hero-title .l2{font-size:30px}
.heading{font-family:"Dosis",sans-serif;font-size:15px;letter-spacing:.3px;color:var(--white);font-weight:400}
.heading.gold{color:var(--gold)}
.hr{height:1px;background:var(--line)}
.cat-list{left:82px;top:440px;width:188px;list-style:none;font-size:10.5px;color:var(--white)}
.cat-list li{height:21.5px;line-height:21px;border-bottom:1px solid var(--line);padding-left:24px;position:relative}
.cat-list li svg{position:absolute;left:7px;top:7px}
.card{left:82px;top:575px;width:172px;height:255px;border:1px solid #444;border-radius:3px;background:#1e1e1e}
.card-title{left:97px;top:586px;font-size:11px;font-weight:600;color:var(--white)}
.ph{background:linear-gradient(160deg,#2b2b2b,#111)}
.price-badge{left:105px;top:718px;width:44px;height:44px;border-radius:50%;background:#fff;color:#222;
  font-size:15px;font-weight:600;text-align:center;line-height:44px}
.btn{height:19px;border:1px solid #bbb;border-radius:2px;background:linear-gradient(#fff,#e2e2e2);
  color:#444;font-size:9px;text-align:center;line-height:17px}
.prod-img{left:312px;top:438px;width:161px;height:163px;border:1px solid #555;border-radius:3px;
  background:radial-gradient(circle at 50% 55%,#4a4028 0%,#2a2c33 55%,#202329 100%)}
.prod-title{left:489px;top:444px;font-size:14px;color:var(--gold);letter-spacing:.2px}
.prod-desc{left:489px;top:465px;width:370px;font-size:10.4px;line-height:15.5px;color:var(--text)}
.prod-price{left:492px;top:502px;font-size:19px;color:var(--white)}
.info{left:310px;top:625px;width:557px;height:431px;border:1px solid #444;border-radius:3px;background:var(--panel)}
.info-head{left:311px;top:626px;width:555px;height:38px;background:var(--panel-head)}
.info-title{left:334px;top:637px;font-size:15px;color:var(--gold)}
.info-body{left:335px;top:681px;width:520px;font-size:10.3px;line-height:15.5px;color:var(--text)}
.info-body p{margin-bottom:15.5px}
.footer-links{left:82px;top:1120px;font-family:"Dosis",sans-serif;font-size:12.5px;color:var(--white)}
.footer-links .bar{margin:0 6px;color:#bbb}
.copy{left:82px;top:1146px;font-size:9px;color:var(--muted)}
.pay{left:706px;top:1122px;display:flex;gap:4px}
.pay span{width:34px;height:21px;border-radius:2px;display:block}
.pay .c1{background:#2b2b2b;border:1px solid #555}
.pay .c2{background:#fff}
.pay .c3{background:#4f8fc8}
.pay .c4{background:#f1f1f1}
</style>
</head>
<body>
<div class="abs header-bg"></div>

<div class="abs logo"><div class="name">Lirvo Dune</div><div class="sub">♦ Jewels ♦</div></div>

<div class="abs social" aria-label="Social links"><span></span><span></span><span></span><span></span></div>

<div class="abs cart">My Cart
  <svg width="18" height="16" viewBox="0 0 18 16" fill="none" stroke="#f2f2f2" stroke-width="1.4"><path d="M1 2h3l2 8h9l2-6H5"/><circle cx="7.5" cy="13.5" r="1.3"/><circle cx="14" cy="13.5" r="1.3"/></svg>
</div>

<div class="abs search">Search here..
  <svg width="15" height="15" viewBox="0 0 15 15" fill="none" stroke="#f2f2f2" stroke-width="1.8"><circle cx="6.3" cy="6.3" r="4.8"/><path d="M10 10l4 4"/></svg>
</div>

<nav class="abs nav">
  <span>HOME</span><span class="sep">♦</span><span>ONLINE SHOP</span><span class="sep">♦</span><span>INFO &amp; FACTS</span><span class="sep">♦</span><span>PARTNER</span><span class="sep">♦</span><span>ABOUT ME</span><span class="sep">♦</span><span>CONTACT</span>
</nav>

<div class="abs hero" role="img" aria-label="Banner photo of a woman wearing a sparkling jewelled bracelet"></div>
<div class="abs hero-title">A DREAM JEWELLERY<br><span class="l2">COLLECTION HERE..</span></div>

<h2 class="abs heading" style="left:85px;top:407px">CATEGORIES</h2>
<div class="abs hr" style="left:82px;top:434px;width:188px"></div>
<ul class="abs cat-list">
  <li><svg width="6" height="8" viewBox="0 0 6 8" fill="none" stroke="#888" stroke-width="1.4"><path d="M1 1l3 3-3 3"/></svg>Collier</li>
  <li><svg width="6" height="8" viewBox="0 0 6 8" fill="none" stroke="#888" stroke-width="1.4"><path d="M1 1l3 3-3 3"/></svg>Bracelet</li>
  <li><svg width="6" height="8" viewBox="0 0 6 8" fill="none" stroke="#888" stroke-width="1.4"><path d="M1 1l3 3-3 3"/></svg>Ring</li>
  <li><svg width="6" height="8" viewBox="0 0 6 8" fill="none" stroke="#888" stroke-width="1.4"><path d="M1 1l3 3-3 3"/></svg>Earring</li>
</ul>

<h2 class="abs heading gold" style="left:82px;top:548px">SHOPPING LIST</h2>
<svg class="abs" style="left:231px;top:551px" width="22" height="11" viewBox="0 0 22 11" fill="none" stroke-width="2"><path d="M7 1L3 5.5 7 10" stroke="#aaa"/><path d="M15 1l4 4.5-4 4.5" stroke="#777"/></svg>

<div class="abs card"></div>
<div class="abs card-title">Anhänger</div>
<div class="abs ph" style="left:96px;top:608px;width:145px;height:175px" role="img" aria-label="Product photo of a beaded silver and gold pendant"></div>
<div class="abs price-badge">275€</div>
<div class="abs btn" style="left:95px;top:792px;width:74px">Product Info</div>

<h2 class="abs heading" style="left:310px;top:403px">PRODUCTS</h2>
<svg class="abs" style="left:826px;top:409px" width="24" height="11" viewBox="0 0 24 11" fill="none" stroke-width="2"><path d="M8 1L4 5.5 8 10" stroke="#aaa"/><path d="M16 1l4 4.5-4 4.5" stroke="#777"/></svg>
<div class="abs hr" style="left:310px;top:426px;width:541px"></div>

<div class="abs prod-img" role="img" aria-label="Product photo of a gold and crystal necklace"></div>
<h3 class="abs prod-title" style="font-weight:400">DUIS TINCIDUNT LECTUS QUIS</h3>
<p class="abs prod-desc">Suspendisse vulputate aliquam dui. Nulla elementum dui ut augue. Aliquam vehicula mi at mauris Maecenas placerat nisl at</p>
<div class="abs prod-price">£25.00</div>
<div class="abs btn" style="left:492px;top:534px;width:74px">Add to Cart</div>

<div class="abs info"></div>
<div class="abs info-head"></div>
<h3 class="abs info-title" style="font-weight:400">PRODUCT INFORMATION</h3>
<div class="abs info-body">
  <p>Preis je Liter: € 12,66</p>
  <p>Dieser Wein ist auch im 6er Karton erhältlich.</p>
  <p>Geschmack:<br>Sehr gefälliger Wein, weich und angenehm, korallrose Farbe und starke fruchtige Noten</p>
  <p>Anbaugebiet:<br>Grumo Lenta, Vessa del Monte</p>
  <p>Rebsorte:<br>Primitivo 50% und Negroamaro 50% der Weinreben Vessa del Monte</p>
  <p>Anbaumethode:<br>Spalier mit Kordon Erziehung</p>
  <p>Boden:<br>Mittlere Dichte, tendenziell kalkhaltig</p>
  <p>Produktionstechnik:<br>Ernte von Hand in Kisten von 25kg, Fermentation in Edelstahl unter Zugabe von ausgewählten Hefen und bei Termperaturen &lt;23°C. Nach dem Ende der alkoholischen Gärung für zwölf Monate gelagert in Edelstahltanks.</p>
</div>

<div class="abs hr" style="left:80px;top:1090px;width:786px"></div>
<div class="abs footer-links">Home<span class="bar">|</span>Online Shop<span class="bar">|</span>Info &amp; Facts<span class="bar">|</span>Partner<span class="bar">|</span>About me<span class="bar">|</span>Contact</div>
<div class="abs copy">© 2013 Company Name. All right reserved</div>
<div class="abs pay" aria-label="Accepted payment cards"><span class="c1"></span><span class="c2"></span><span class="c3"></span><span class="c4"></span></div>
</body>
</html>
```